Verodex business card

Business card for sustainable investment company called "Verodex". Verodex is an exchange platform selling carbon credits between buyers and sellers. Carbon Credits are an environmental commodity for reducing global carbon emissions.

the card should obviously have our logo and the theme should be sustainability/environment mixed with a trading platform.

Contact Information for Business Card

Logo, Name, Title, Phone, Email

Colors
0054AA
0677BA
7BADD7
CADEEF
E8F1F8
0094D4
00A9DD
6FCCEA
C7EBF8
E9F6FB
00AB8E
00BBA5
67D7C9
C6EFE9
E9F9F6
59FF00
82FF00
B8FF75
E3FFCB
F4FFEA

```html
<!DOCTYPE html>
<html lang="en">
<head>
<meta charset="utf-8">
<title>Verodex Business Card</title>
<link href="https://fonts.googleapis.com/css2?family=Raleway:wght@700;800&family=Montserrat:wght@400;500&family=Pinyon+Script&display=swap" rel="stylesheet">
<style>
  :root {
    --backdrop: #262626;
    --navy-deep: #12235a;
    --navy-mid: #1c2d66;
    --navy-violet: #434d94;
    --navy-text: #16295a;
    --sky: #6fcbe6;
    --azure: #4a8fd4;
    --card-white: #ffffff;
  }
  * { margin: 0; padding: 0; box-sizing: border-box; }
  html, body {
    width: 900px;
    height: 1200px;
    overflow: hidden;
    background: var(--backdrop);
  }
  .canvas {
    position: relative;
    width: 900px;
    height: 1200px;
  }
  .card {
    position: absolute;
    left: 90px;
    width: 720px;
  }
  .card-front {
    top: 151px;
    height: 408px;
    background: linear-gradient(90deg, var(--navy-deep) 0%, var(--navy-mid) 45%, var(--navy-violet) 100%);
    overflow: hidden;
  }
  .pattern-field {
    position: absolute;
    inset: 0;
    background:
      radial-gradient(ellipse at 85% 40%, rgba(110, 120, 190, 0.35) 0%, rgba(110, 120, 190, 0) 60%),
      linear-gradient(180deg, rgba(255, 255, 255, 0.04) 0%, rgba(0, 0, 0, 0.12) 100%),
      linear-gradient(90deg, #0f1f55 0%, #1d2e68 50%, #3d4890 85%, #4a55a0 100%);
  }
  .front-mark {
    position: absolute;
    left: 540px;
    top: 296px;
    width: 86px;
    height: 54px;
    display: flex;
    align-items: center;
    justify-content: center;
    font-family: 'Raleway', sans-serif;
    font-weight: 800;
    font-size: 22px;
    line-height: 1;
    color: var(--sky);
  }
  .card-back {
    top: 615px;
    height: 433px;
    background: var(--card-white);
    text-align: center;
    color: var(--navy-text);
  }
  .brand-square {
    position: absolute;
    left: 328px;
    top: 52px;
    width: 64px;
    height: 64px;
    background: var(--azure);
  }
  .company-name {
    position: absolute;
    left: 0; right: 0;
    top: 136px;
    font-family: 'Raleway', sans-serif;
    font-weight: 800;
    font-size: 54px;
    line-height: 1;
    letter-spacing: 1px;
    color: var(--navy-text);
  }
  .person-name {
    position: absolute;
    left: 0; right: 0;
    top: 252px;
    font-family: 'Raleway', sans-serif;
    font-weight: 700;
    font-size: 29px;
    line-height: 1;
    color: var(--azure);
  }
  .person-title {
    position: absolute;
    left: 0; right: 0;
    top: 288px;
    font-family: 'Pinyon Script', cursive;
    font-size: 21px;
    line-height: 1;
    color: var(--navy-text);
  }
  .contact-line {
    position: absolute;
    left: 0; right: 0;
    font-family: 'Montserrat', sans-serif;
    font-weight: 500;
    line-height: 1;
    color: var(--navy-text);
  }
  .contact-primary {
    top: 329px;
    font-size: 17px;
    letter-spacing: 3px;
  }
  .contact-primary .divider {
    display: inline-block;
    width: 2px;
    height: 22px;
    background: var(--azure);
    vertical-align: middle;
    margin: 0 14px 0 10px;
    position: relative;
    top: -2px;
  }
  .contact-primary .phone {
    font-size: 20px;
    letter-spacing: 5px;
  }
  .contact-email {
    top: 367px;
    font-size: 16px;
    letter-spacing: 4px;
  }
</style>
</head>
<body>
<main class="canvas">
  <section class="card card-front">
    <div class="pattern-field" role="img" aria-label="Embossed repeating brand pattern on deep navy, fading to violet on the right"></div>
    <span class="front-mark">VERODEX</span>
  </section>

  <section class="card card-back">
    <span class="brand-square" aria-hidden="true"></span>
    <h1 class="company-name">VERODEX</h1>
    <p class="person-name">DANIEL REYES</p>
    <p class="person-title">Founder</p>
    <p class="contact-line contact-primary">WWW.VERODEX.COM<span class="divider"></span><span class="phone">303-555-0142</span></p>
    <p class="contact-line contact-email">INFO@VERODEX.COM</p>
  </section>
</main>
</body>
</html>
```